The Harlow Reserve Web Site design

I need a web design for my luxury range of Terry Toweling and Spa Accessories for luxury upmarket hotels and Spas. I have a catalog that sets the mood and tone I am looking for. I need a website design that shows off the look and feel of this luxury range while working back to the catalog look and feel. Its all about Upmarket and Luxury. I will be using the website as a reference site and as a site that customers can purchase off.
The Logo is attached as is the catalog. I don't mind changing the color of the Logo to match the website. However I would prefer to keep the font of that logo.

http://thegallerydesk.pixvault-example.com/p504729381
Please can you try and access this link. The Harlow Reserve
Name Greta. Email greta@vellumsupply-example.com.au. Password Harlow.
These images are to be used for shopping page and please use the close up details of texture as background on pages and use those texture details and close ups for banners

Please note the look and feel has to be very upmarket and super luxury. Ficus is on mood and not on retail.
Have a look at the mood on the following websites
Www.gracefulretreats-example.com
And yourcosyseasidecabin-example.com
That one is retail .mi don't want retail focus but it's very clean. And simple and colors are good
Updates

Please rebook brief. I have added some important detail. Thanks

Relook brief. I have added,important detail. Thanks

Target Market(s)

Corporate buyers
This is not for retail selling to consumers
Price it's viewed only after secure login

Industry/Entity Type

Shopping

Colors
acd037
cadf82
fbc995
fce7d3
faa54b

Requirements
Must have
• Luxury. Think luxury. Very high end yet modern like the catalogue
Use banners on home page
Should not have
• Don't use the blue as the main color. It's too cheap.
No products on home page

```html
<!DOCTYPE html>
<html lang="en">
<head>
<meta charset="utf-8">
<title>The Harlow Reserve</title>
<link href="https://fonts.googleapis.com/css2?family=Open+Sans:ital,wght@0,400;0,600;0,700;1,400;1,700&family=Questrial&display=swap" rel="stylesheet">
<style>
:root{
  --leaf:#acd037;
  --leaf-soft:#cadf82;
  --leaf-deep:#6e9a14;
  --peach:#f9c896;
  --cream:#fce7d3;
  --ink:#1e1e1e;
  --slate:#7a7a7a;
  --lavender:#c9cbff;
  --brand-blue:#1b6fa8;
  --alert-red:#d8141a;
  --alert-gold:#ffe31a;
  --white:#ffffff;
}
*{margin:0;padding:0;box-sizing:border-box}
html,body{width:1200px;height:1000px;overflow:hidden;background:var(--white)}
body{position:relative;font-family:"Open Sans",Arial,sans-serif;color:var(--white)}
.abs{position:absolute}

/* header */
.hero{left:280px;top:0;width:645px;height:325px;
  background:radial-gradient(ellipse at 60% 35%,#f2f9c4 0%,#c7e36a 35%,#8fbd2a 70%,#5f8f1c 100%)}
.hero-scene{left:252px;top:178px;width:673px;height:147px;
  background:linear-gradient(90deg,#d8dcd8 0%,#b9b6ae 20%,#9fc24a 45%,#e9ece6 60%,#a4c84a 75%,#8b8276 100%);opacity:.85}
.top-strip{left:280px;top:0;width:640px;height:12px;background:var(--leaf-deep)}
.top-links{left:700px;top:1px;font-size:5.5px;font-weight:700;display:flex;gap:6px;align-items:center}
.top-links .dot{width:9px;height:9px;border-radius:50%;background:#e8f2ff}
.top-links .pill{background:#2b2b2b;border-radius:5px;padding:0 8px;line-height:8px}
.brand{left:280px;top:25px;width:282px;height:21px;background:linear-gradient(90deg,var(--white) 85%,rgba(255,255,255,0))}
.brand span{position:absolute;left:12px;top:-3px;font-family:"Questrial",sans-serif;font-size:21px;color:var(--brand-blue);white-space:nowrap}
.call{left:716px;top:30px;font-size:10px;font-weight:700;letter-spacing:1.3px;word-spacing:3px}
.nav{left:280px;top:62px;width:638px;height:18px;background:rgba(170,210,60,.75);display:flex;align-items:center;padding-left:17px;gap:12px;font-size:8.5px;font-weight:700;white-space:nowrap}
.intro-title{left:297px;top:101px;font-size:10.5px}
.intro-text{left:298px;top:122px;width:300px;font-size:7px;line-height:9.5px;color:#2a2f1a}

/* collections */
.band{left:275px;width:650px}
.band.blankets{top:324px;height:165px;background:var(--ink)}
.band.robes{top:489px;left:274px;height:161px;background:var(--peach)}
.thumb{border:3px solid var(--white);border-radius:6px;box-shadow:0 0 4px rgba(0,0,0,.35)}
.thumb.blankets{left:430px;top:335px;width:121px;height:146px;background:linear-gradient(160deg,#3b4148,#9aa0a6 55%,#e0e0e0)}
.thumb.robes{left:428px;top:494px;width:123px;height:151px;background:linear-gradient(150deg,#2c5c8c,#d8d2c6 50%,#b5a48a)}
.col-title{font-style:italic;font-weight:700;white-space:nowrap}
.blankets-title{left:558px;top:349px;font-size:15.5px}
.robes-title{left:563px;top:530px;font-size:14px;letter-spacing:4px}
.col-list{list-style:none;font-style:italic;white-space:nowrap}
.blankets-list{left:558px;top:383px;font-size:10px;line-height:21px}
.robes-list{left:563px;top:563px;font-size:10px;line-height:21px}

/* partners */
.partners{left:297px;top:671px;width:593px;height:84px;background:linear-gradient(180deg,var(--cream) 0%,var(--peach) 14%,var(--leaf-soft) 40%,var(--leaf) 100%)}
.badge{top:683px;width:112px;height:58px;background:var(--white);border:2px solid #222;border-radius:3px;box-shadow:3px 3px 4px rgba(0,0,0,.35);display:flex;align-items:center;justify-content:center}
.badge i{display:block;width:60px;height:22px;background:#d6d6d6}

/* footer */
.footer{left:280px;top:775px;width:640px;height:225px;background:var(--slate)}
.footer-rule{left:280px;top:924px;width:640px;height:2px;background:#a9a9a9}
.foot-head{font-size:13.5px;color:var(--lavender);font-family:"Questrial",sans-serif}
.foot-list{list-style:none;font-size:8.5px;font-weight:700}
.sitemap-list{left:348px;top:800px;line-height:13.3px}
.extra-list{left:540px;top:802px;font-size:7.5px;line-height:15.2px}
.contact-text{left:690px;top:802px;font-size:7.5px;font-weight:700;line-height:13px}
.order-btn{left:687px;top:888px;width:210px;height:18px;background:linear-gradient(180deg,#ff4a4a,var(--alert-red));border:1px solid #300;border-radius:5px;color:var(--alert-gold);font-weight:700;font-size:12.5px;text-align:center;line-height:16px;letter-spacing:.5px}
.promo{left:388px;top:936px;width:424px;font-size:7.3px;line-height:10.5px;color:var(--peach);font-weight:600;text-align:justify}
</style>
</head>
<body>
<div class="abs hero" role="img" aria-label="Spa scene with bamboo and calm water in fresh greens"></div>
<div class="abs hero-scene" role="img" aria-label="Guest resting on a white robe beside stacked stones, folded towels and a draped lounge chair"></div>
<div class="abs top-strip"></div>
<div class="abs top-links"><span>Follow Us on:</span><span class="dot"></span><span class="dot"></span><span class="pill">Login</span><span class="pill">Contact Us</span><span class="pill">Search</span></div>
<div class="abs brand"><span>The Harlow Reserve</span></div>
<div class="abs call">Call to order: 1-877-555-0142</div>
<nav class="abs nav"><span>Home</span><span>Bath towels</span><span>Robes</span><span>Accessories</span><span>Mats</span><span>Pool &amp; Beach</span><span>Blankets &amp; Throws</span><span>Massage &amp; Sauna</span><span>New Collection</span></nav>
<div class="abs intro-title">Wrap yourself in luxury...</div>
<p class="abs intro-text">Here at The Harlow Reserve we deliver the finest in cotton towels, loungewear, and bath accessories to ensure that your bath and spa collection not only looks great, but also offers supreme comfort, absorbency, and durability.</p>

<section class="abs band blankets"></section>
<div class="abs thumb blankets" role="img" aria-label="Made bed dressed in grey blankets and white pillows"></div>
<h2 class="abs col-title blankets-title">Blankets and Throws</h2>
<ul class="abs col-list blankets-list">
  <li>Baby Skin 600 Thread Counts* / Tacto Pétalo de Rosa 600 Hilos</li>
  <li>Stripe 300 Thread Counts* / Raya 300 Hilos</li>
  <li>Percale 200 Thread Counts* / Percal 200 Hilos</li>
  <li>Crochet Blanket / Manta Crochet</li>
</ul>

<section class="abs band robes"></section>
<div class="abs thumb robes" role="img" aria-label="Guest seated in a white terry robe"></div>
<h2 class="abs col-title robes-title">Robes</h2>
<ul class="abs col-list robes-list">
  <li>Oriental Kimono Robe / Albornoz Kimono</li>
  <li>Canelado Shawl Collar Robe &nbsp;/ Albornoz Smoking</li>
</ul>

<div class="abs partners"></div>
<div class="abs badge" style="left:321px"><i></i></div>
<div class="abs badge" style="left:457px"><i></i></div>
<div class="abs badge" style="left:603px"><i></i></div>
<div class="abs badge" style="left:748px"><i></i></div>

<footer class="abs footer"></footer>
<div class="abs footer-rule"></div>
<h3 class="abs foot-head" style="left:347px;top:780px">Site Map</h3>
<h3 class="abs foot-head" style="left:540px;top:781px">Aditional</h3>
<h3 class="abs foot-head" style="left:689px;top:780px">Contact</h3>
<ul class="abs foot-list sitemap-list">
  <li>Home</li><li>Bath towels</li><li>Robes</li><li>Accessories</li><li>Mats</li><li>Pool &amp; Beach</li><li>Blankets &amp; Throws</li><li>Massage &amp; Sauna</li><li>New Collection</li>
</ul>
<ul class="abs foot-list extra-list">
  <li>About Us</li><li>Customer Service</li><li>Wholesalers</li><li>Contact Us</li><li>Email registration</li><li>Privacy Policy</li>
</ul>
<div class="abs contact-text">
  <p>Postal address: 4810 Linden Row, Coral Bay, FL</p>
  <p style="margin-top:13px">eMail: contact@theharlowreserve-example.com</p>
  <p style="margin-top:12px">Phone: (305) 555-0118, Fax: (305) 555-0190,</p>
  <p style="margin-top:2px">Toll Free: (877) 6 HARLOW or (877) 555-0142</p>
</div>
<div class="abs order-btn">Call to Order: 1.877.555.0142</div>
<p class="abs promo">Receive 1 free identical robe with your valid purchase of 1 ROBE on theharlowreserve-example.com. Free robe will be identical in style and size. Promotion will be valid from Feburary 4, 2014 12:00 AM EST through Feburary 13th, 2014 11:59PM EST. Promotion will not be granted, may be revoked, and may not be redeemed for a future purchase if the initial transaction is cancelled or a refund is issued. Promotion may be suspended or terminated at any time. Promotion not valid on third-party sites.</p>
</body>
</html>
```